Business Card Design - ChoiceCraft

Looking for creative, modern design, two sided for ChoiceCraft that is consistent with color and feel of website www.choicecraftpro.net.
Updates

Back of card will be used to promote products or have a quote revolving around decisions, change, leadership, innovation, creativity. Back should also have space to promote website, but optional to use the icon. Front of the card will need to use the icon and have standard place for name, job title, phone and email. We are not looking to put a mailing address or fax. Also want space to place a few words/phrase explaining what we do...such as individual growth and organizational development or tools, training, information...in addition, want the facebook icon small on the front somewhere as we are also on facebook.

Vector file uploaded of icon.

Target Market(s)

Professional coaching for individual growth and organizational development

Industry/Entity Type

Business

Requirements
Must have
• Icon...see attached.

```html
<!DOCTYPE html>
<html lang="en">
<head>
<meta charset="utf-8">
<title>ChoiceCraft Business Card</title>
<link href="https://fonts.googleapis.com/css2?family=Tinos:wght@400;700&family=Arimo:wght@400;700&display=swap" rel="stylesheet">
<style>
  :root {
    --backdrop: #d9dcdf;
    --card-white: #ffffff;
    --brand-blue: #1d6fb8;
    --navy: #232a7a;
    --sky: #29b3ea;
    --sky-light: #8ed3f2;
    --deep-blue: #0f6dbd;
    --text-light: #ffffff;
  }
  * { margin: 0; padding: 0; box-sizing: border-box; }
  html, body { width: 1200px; height: 1076px; overflow: hidden; }
  body { background: var(--backdrop); position: relative; font-family: "Tinos", "Times New Roman", serif; }

  .card { position: absolute; overflow: hidden; box-shadow: 0 2px 6px rgba(0,0,0,.25); }
  .card-front { left: 64px; top: 68px; width: 797px; height: 455px; background: var(--card-white); }
  .card-back { left: 330px; top: 564px; width: 794px; height: 453px;
    background: linear-gradient(120deg, var(--sky) 0%, var(--sky) 55%, var(--sky-light) 100%); }

  .front-wave { position: absolute; inset: 0; }

  .brand-mark { position: absolute; border-radius: 50%;
    background: radial-gradient(circle at 40% 35%, #e6eef6 0%, #9fb4c9 55%, #2e86d6 100%); }
  .card-front .brand-mark { left: 174px; top: 53px; width: 166px; height: 166px; }
  .card-back .brand-mark { left: 561px; top: 262px; width: 136px; height: 136px; }

  .brand-name { position: absolute; left: 348px; top: 106px; font-family: "Tinos", serif;
    font-weight: 700; font-size: 37px; color: var(--brand-blue); letter-spacing: .3px; }

  .person { position: absolute; left: 0; width: 797px; top: 254px; text-align: center;
    color: var(--navy); font-size: 27px; font-weight: 700; padding-left: 0; }
  .person .title { font-weight: 400; font-size: 19px; }

  .tagline { position: absolute; right: 427px; top: 350px; text-align: right;
    color: var(--text-light); font-size: 19px; line-height: 23px; }

  .divider { position: absolute; left: 389px; top: 332px; width: 1px; height: 106px; background: rgba(255,255,255,.7); }

  .contacts { position: absolute; left: 406px; top: 338px; list-style: none; color: var(--text-light);
    font-size: 19px; line-height: 24px; }
  .contacts li { display: flex; align-items: center; gap: 8px; }
  .contacts svg { width: 15px; height: 15px; flex: none; }
  .social-square { width: 13px; height: 13px; background: var(--text-light); flex: none; margin: 0 1px; }

  .quotes { position: absolute; left: 56px; top: 40px; list-style: none; font-family: "Arimo", Arial, sans-serif; color: var(--text-light); }
  .quote { position: relative; padding-left: 26px; margin-bottom: 26px; }
  .quote-text { font-size: 20px; line-height: 26px; }
  .quote-text::before { content: "\201C"; position: absolute; left: 0; top: -6px; font-family: "Tinos", serif; font-size: 34px; font-weight: 700; }
  .quote-text::after { content: "\201D"; font-family: "Tinos", serif; font-size: 34px; font-weight: 700; vertical-align: -14px; margin-left: 2px; }
  .quote-author { font-size: 20px; font-weight: 700; line-height: 26px; }
</style>
</head>
<body>

<section class="card card-front" aria-label="Card front">
  <svg class="front-wave" width="797" height="455" viewBox="0 0 797 455" aria-hidden="true">
    <defs>
      <linearGradient id="front-blue" x1="0" x2="1" y1="0" y2="0">
        <stop offset="0" stop-color="#35b6ec"/>
        <stop offset="1" stop-color="#0f6dbd"/>
      </linearGradient>
    </defs>
    <path d="M0,238 Q398,372 797,236 L797,455 L0,455 Z" fill="#232a7a"/>
    <path d="M0,250 Q398,382 797,246 L797,455 L0,455 Z" fill="url(#front-blue)"/>
  </svg>

  <div class="brand-mark" aria-hidden="true"></div>
  <div class="brand-name">ChoiceCraft</div>

  <p class="person">Your Name, <span class="title">Title</span></p>

  <p class="tagline">Supporting individual growth<br>and organizational development<br>or tools, training, information</p>

  <div class="divider"></div>

  <ul class="contacts">
    <li>
      <svg viewBox="0 0 16 16" aria-hidden="true"><circle cx="8" cy="8" r="7" fill="none" stroke="#fff" stroke-width="1.4"/><path d="M5.5 4.5l1.5 1.5-1 1c.6 1.3 1.5 2.2 2.8 2.8l1-1 1.5 1.5-1 1.2C7.5 11.3 4.7 8.5 4.3 5.7z" fill="#fff"/></svg>
      123-456-789
    </li>
    <li>
      <svg viewBox="0 0 16 16" aria-hidden="true"><rect x="1.5" y="4" width="13" height="9" fill="none" stroke="#fff" stroke-width="1.4"/><path d="M1.5 4l6.5 5 6.5-5" fill="none" stroke="#fff" stroke-width="1.4"/></svg>
      info@choicecraftmail.com
    </li>
    <li>
      <svg viewBox="0 0 16 16" aria-hidden="true"><circle cx="8" cy="8" r="6.5" fill="none" stroke="#fff" stroke-width="1.3"/><ellipse cx="8" cy="8" rx="2.8" ry="6.5" fill="none" stroke="#fff" stroke-width="1.1"/><path d="M1.5 8h13" stroke="#fff" stroke-width="1.1"/></svg>
      www.choicecraftpro.net
    </li>
    <li>
      <span class="social-square" aria-hidden="true"></span>
      /choicecraftpro
    </li>
  </ul>
</section>

<section class="card card-back" aria-label="Card back">
  <ul class="quotes">
    <li class="quote">
      <p class="quote-text">Try not to become a man of success, but rather a man of value.</p>
      <p class="quote-author">- Arlen Whitcombe</p>
    </li>
    <li class="quote">
      <p class="quote-text">The only constant is change.</p>
      <p class="quote-author">- Theron of Kos</p>
    </li>
    <li class="quote">
      <p class="quote-text">We are what we repeatedly do. Excellence is not an act, it is a habit.</p>
      <p class="quote-author">- Philon Marek</p>
    </li>
    <li class="quote">
      <p class="quote-text">Simplicity is the ultimate sophistication.</p>
      <p class="quote-author">- Lorenzo Vellani</p>
    </li>
    <li class="quote">
      <p class="quote-text">Life is not fair - get used to it.</p>
      <p class="quote-author">- Walt Brenner</p>
    </li>
  </ul>
  <div class="brand-mark" aria-hidden="true"></div>
</section>

</body>
</html>
```